Hardcore nerd needs to stand out in a sea of dull Defence business cards

Wombarra Devices is a new Australian consulting engineering company that turns research and theory into practical systems. No evangelistic fluff, just mathematics and physics into electronic and optical circuits for consumer products, scientific research or Defence applications.

We already have a recognised logo (provided) which is often dark blue/black on a light background but we're open to other combinations. (Us engineers tend to have limited aesthetic imagination :)

Some of our recent products have included:
* Instrumentation for electrical testing,
* Radar jammers,
* GPS antenna design,
* Satellite tracking systems,
* High power lasers

We're open to both single and double-sided designs - happy to be convinced either way.

P.S. Another group is working on the web page, so - alas - our web site is currently of no use for images/ideas...

Target Market(s)

Engineering managers,
Scientists

Contact Information for Business Card

Dr Colin Harte
R&D Engineer

colin@wombarradevices.com.au
0427 563 710

PO Box XXX (to be confirmed)
Kelsby ACT 2917
Australia

Font styles to use
Serif
Sans Serif

Colors

Designer to choose colors to be used in the design.

Requirements
Must have
• My contact details!
• I've had many (great) "bold and plain" designs submitted already, so feel free to be artistically creative :)
• Happy to take advice re fonts/colours/printability etc.
Nice to have
• I'm not sure if "lists" are more at home on a CV than a business card, but representative services include:
• Applied electromagnetics
• RF and high speed electronics
• Signal and image processing
• Electro-optical and laser systems
• Concept-to-prototype design services
• If you're considering double sided cards, then often measuring/alignment grids/rulers feature on the back of similar cards.
• e.g. https://www.veltranoptics.example/newgrouppage9.cfm?objectgroup_id=4183
• https://www.veltranoptics.example/newgrouppage9.cfm?objectgroup_ID=4185
• ..or even a "Smith chart" (google will return lots)
• Generic images to represent a capability might work - googling images associated with keyword for each of these areas might help:
• - "passive radar", "phased array", "fdtd", "vircator"
• RF and high speed electronic design
• - "smith chart", "microstrip circuits", "dimensioned drawing", "electronic schematic"
• - "dft", "iir filter"
• - "optical cavity". "laser energy level diagram"
• Background/watermarked images outlines/wireframes/schematics would probably look OK.
Should not have
• If a list of projects/services is provided, it is important not to make the client feel that this is "all" the company can do. Engineering design is a creative discipline (like graphics :)
• Please, no stock "military" snaps like planes, missiles, etc!

```html
<!DOCTYPE html>
<html lang="en">
<head>
<meta charset="utf-8">
<title>Wombarra Devices – Business Card</title>
<link rel="stylesheet" href="https://fonts.googleapis.com/css2?family=Arimo:wght@700&family=Lato:wght@400;700;900&display=swap">
<style>
  :root {
    --navy: #03205f;
    --navy-ink: #0a1f5c;
    --paper: #ffffff;
    --backdrop: #e6e4e0;
    --rule: #5f76b0;
    --text-light: #ffffff;
    --text-dark: #1b1f2e;
  }
  * { margin: 0; padding: 0; box-sizing: border-box; }
  html, body {
    width: 1200px; height: 900px; overflow: hidden;
    background: var(--backdrop);
  }
  .canvas { position: relative; width: 1200px; height: 900px; }

  .card {
    position: absolute;
    left: 330px;
    width: 556px;
    height: 344px;
  }

  /* Front side */
  .card--front {
    top: 90px;
    background: var(--navy);
    color: var(--text-light);
    text-align: center;
    font-family: "Lato", sans-serif;
  }
  .holder-name {
    position: absolute; top: 156px; left: 0; right: 0;
    font-family: "Arimo", sans-serif; font-weight: 700;
    font-size: 21px; letter-spacing: 0.2px;
  }
  .card--front .holder-name { top: 66px; }
  .holder-role { position: absolute; top: 89px; left: 0; right: 0; font-size: 15px; }
  .contact-icons {
    position: absolute; top: 121px; left: 188px; width: 178px; height: 22px;
  }
  .contact-lines {
    position: absolute; top: 150px; left: 0; right: 0;
    font-size: 16px; line-height: 20.5px;
  }
  .divider {
    position: absolute; top: 224px; left: 188px; width: 184px; height: 1px;
    background: var(--rule);
  }
  .postal-lines {
    position: absolute; top: 235px; left: 0; right: 0;
    font-size: 16px; line-height: 20.5px;
  }

  /* Back side */
  .card--back {
    top: 469px;
    background: var(--paper);
    font-family: "Lato", sans-serif;
  }
  .brand {
    position: absolute; top: 89px; left: 108px;
    display: flex; align-items: center; gap: 14px;
  }
  .brand-dot {
    width: 116px; height: 116px; border-radius: 50%;
    background: var(--navy-ink);
  }
  .brand-name {
    color: var(--navy-ink); font-weight: 900; line-height: 1;
  }
  .brand-name .line-1 { display: block; font-size: 39px; letter-spacing: 0.5px; }
  .brand-name .line-2 { display: block; font-size: 24px; letter-spacing: 4.6px; margin-top: 6px; }
  .services {
    position: absolute; top: 268px; left: 42px;
    display: grid; grid-template-columns: 222px auto;
    row-gap: 1px; list-style: none;
    font-size: 16px; line-height: 20px; color: var(--text-dark);
  }
  .services li::before {
    content: ""; display: inline-block; width: 7px; height: 7px;
    border-radius: 50%; background: var(--navy-ink);
    margin-right: 5px; vertical-align: 2px;
  }
</style>
</head>
<body>
<main class="canvas">
  <section class="card card--front" aria-label="Card front">
    <h1 class="holder-name">DR COLIN HARTE</h1>
    <p class="holder-role">R&amp;D Engineer</p>
    <svg class="contact-icons" viewBox="0 0 178 22" aria-hidden="true">
      <line x1="0" y1="11" x2="52" y2="11" stroke="#8a9cc8" stroke-width="1"/>
      <line x1="126" y1="11" x2="178" y2="11" stroke="#8a9cc8" stroke-width="1"/>
      <g fill="#fff">
        <circle cx="63" cy="11" r="11"/>
        <circle cx="89" cy="11" r="11"/>
        <circle cx="115" cy="11" r="11"/>
      </g>
      <g fill="none" stroke="#03205f" stroke-width="1.6">
        <path d="M56 9 q7 -5 14 0 M58 10 h10 v6 h-10 z"/>
        <rect x="82" y="6.5" width="14" height="9" rx="1"/>
        <path d="M82 7 l7 5 l7 -5"/>
        <circle cx="115" cy="11" r="6.5"/>
        <path d="M108.5 11 h13 M115 4.5 q-4 6.5 0 13 q4 -6.5 0 -13"/>
      </g>
    </svg>
    <p class="contact-lines">0427 563 710<br>colin@wombarradevices.com.au<br>www.wombarradevices.com.au</p>
    <div class="divider"></div>
    <p class="postal-lines">PO Box XXX<br>Kelsby ACT 2917, Australia</p>
  </section>

  <section class="card card--back" aria-label="Card back">
    <div class="brand">
      <span class="brand-dot" aria-hidden="true"></span>
      <p class="brand-name"><span class="line-1">WOMBARRA</span><span class="line-2">DEVICES</span></p>
    </div>
    <ul class="services">
      <li>Applied electromagnetics</li>
      <li>RF and high speed electronics</li>
      <li>Signal and image processing</li>
      <li>Electro-optical and laser systems</li>
    </ul>
  </section>
</main>
</body>
</html>
```